Oil and Gas Exploration and Production company needs a business card design

We need a business card design using our logo and colors in the logo. We want a mainstream design.

```html
<!DOCTYPE html>
<html lang="en">
<head>
<meta charset="utf-8">
<title>Solara Oil &amp; Gas – Business Card</title>
<link href="https://fonts.googleapis.com/css2?family=Work+Sans:wght@400;500;600&display=swap" rel="stylesheet">
<style>
  :root {
    --backdrop: #1c1c1c;
    --card: #232323;
    --card-edge: #2c2c2c;
    --gold: #d9a21b;
    --gold-glow: rgba(217, 162, 27, 0.55);
    --white: #f4f4f4;
    --pattern-dark: #1f1f1f;
    --pattern-mid: #3b3b3b;
    --pattern-light: #7d7d7d;
  }
  * { margin: 0; padding: 0; box-sizing: border-box; }
  html, body {
    width: 1200px; height: 900px; overflow: hidden;
    background: var(--backdrop);
    font-family: "Work Sans", sans-serif;
  }
  .canvas {
    position: relative; width: 1200px; height: 900px;
    display: flex; flex-direction: column; align-items: center; justify-content: center; gap: 32px;
  }
  .card {
    width: 700px; height: 400px;
    background: var(--card);
    border: 1px solid var(--card-edge);
    border-radius: 4px;
    position: relative; overflow: hidden;
  }
  .card-back { background: var(--pattern-dark); }
  .card-back-pattern {
    position: absolute; inset: 0;
    background:
      radial-gradient(circle at 46% 46%, var(--gold-glow) 0, rgba(217, 162, 27, 0.18) 30px, rgba(217, 162, 27, 0) 60px),
      linear-gradient(115deg, var(--pattern-dark) 0%, var(--pattern-dark) 22%, var(--pattern-mid) 52%, var(--pattern-light) 100%);
  }
  .card-front { display: flex; align-items: center; }
  .brand {
    width: 345px; padding-left: 62px;
    display: flex; align-items: center; gap: 14px;
  }
  .brand-dot { width: 24px; height: 24px; border-radius: 50%; background: var(--white); flex: none; }
  .brand-name {
    font-weight: 600; font-size: 42px; line-height: 1.05; color: var(--white);
    letter-spacing: 0.3px;
  }
  .divider { width: 3px; height: 178px; background: var(--gold); margin-right: 34px; }
  .contact { color: var(--white); }
  .contact-name { font-size: 32px; font-weight: 600; color: var(--gold); line-height: 1.1; }
  .contact-role { font-size: 16px; margin-bottom: 18px; letter-spacing: 0.5px; }
  .contact-address { font-size: 17px; line-height: 1.35; margin-bottom: 14px; letter-spacing: 0.5px; }
  .contact-line { display: flex; align-items: center; gap: 10px; font-size: 18px; line-height: 1.45; letter-spacing: 0.5px; }
  .contact-line svg { width: 13px; height: 13px; flex: none; }
  .accent { color: var(--gold); }
</style>
</head>
<body>
<main class="canvas">
  <section class="card card-back">
    <div class="card-back-pattern" role="img" aria-label="Embossed repeating pattern of the company emblem in greys, dark on the left and lighter to the right, with a single emblem picked out in gold near the centre"></div>
  </section>

  <section class="card card-front">
    <div class="brand">
      <span class="brand-dot"></span>
      <span class="brand-name">Solara<br>Oil &amp; Gas</span>
    </div>
    <div class="divider"></div>
    <div class="contact">
      <p class="contact-name">Dale Whitmore</p>
      <p class="contact-role">CFO</p>
      <p class="contact-address">2450 Mesa Ridge Rd,<br>Abilene, Texas us</p>
      <p class="contact-line">
        <svg viewBox="0 0 16 16" aria-hidden="true"><path d="M3 1.5l3 .5 1 3.5-2 1.2a9 9 0 004.3 4.3l1.2-2 3.5 1 .5 3c-7 1.5-13-4.5-11.5-11.5z" fill="none" stroke="#d9a21b" stroke-width="1.5"/></svg>
        (555) 482-7730
      </p>
      <p class="contact-line">
        <svg viewBox="0 0 16 16" aria-hidden="true"><rect x="1.5" y="3.5" width="13" height="9" fill="none" stroke="#d9a21b" stroke-width="1.4"/><path d="M1.5 3.5l6.5 5 6.5-5" fill="none" stroke="#d9a21b" stroke-width="1.4"/></svg>
        info@solaraoil.com
      </p>
      <p class="contact-line">
        <svg viewBox="0 0 16 16" aria-hidden="true"><circle cx="8" cy="8" r="6.5" fill="none" stroke="#d9a21b" stroke-width="1.4"/><ellipse cx="8" cy="8" rx="2.8" ry="6.5" fill="none" stroke="#d9a21b" stroke-width="1.2"/><path d="M1.5 8h13" stroke="#d9a21b" stroke-width="1.2"/></svg>
        <span>www.<span class="accent">solaraoil</span>.com</span>
      </p>
    </div>
  </section>
</main>
</body>
</html>
```